Business Card Design Project

I have established a company called "Corvella" which is a business specialising in psychotherapy/counselling , predominantly for anxiety & depression.

My name is Nel....hence, the Corvella link. However, Corvella was also chosen for its reference to green shoots of growth/recovery.

Corvella is to be "upmarket" and highly professional. I'm keen for the style and colours to reflect this.....taupe/grey with navy/black script, for example.....NO primary colours.

My name needs to be on the card and my mobile number. Not sure, but suspect it should also have my qualifications ( BA (Psych) & BSc (Hons) Psychology). Mobile number 0412 903 618.

```html
<!DOCTYPE html>
<html lang="en">
<head>
<meta charset="utf-8">
<title>Corvella — Business Card Front</title>
<link href="https://fonts.googleapis.com/css2?family=Federo&family=Tenor+Sans&family=Lato:wght@400&display=swap" rel="stylesheet">
<style>
  :root {
    --page-bg: #f2f2f2;
    --brand-green: #9cc25a;
    --name-light: #e6ecf5;
    --ink-dark: #12141f;
    --ink-light: #ffffff;
    --card-slate: #3f6791;
    --card-navy: #2a2f5c;
    --card-taupe: #9a7f6c;
  }
  html, body {
    margin: 0;
    padding: 0;
    width: 1026px;
    height: 1200px;
    overflow: hidden;
    background: var(--page-bg);
  }
  .canvas {
    position: relative;
    width: 1026px;
    height: 1200px;
  }
  .business-card {
    position: absolute;
    left: 63px;
    top: 352px;
    width: 900px;
    height: 497px;
    display: block;
    box-shadow: 0 10px 28px rgba(0, 0, 0, 0.35);
  }
  .brand-name {
    font-family: "Federo", sans-serif;
    fill: var(--brand-green);
  }
  .person-name {
    font-family: "Tenor Sans", sans-serif;
    fill: var(--name-light);
  }
  .credentials,
  .contact {
    font-family: "Lato", sans-serif;
    fill: var(--ink-dark);
  }
  .tagline {
    font-family: "Lato", sans-serif;
    fill: var(--ink-light);
  }
</style>
</head>
<body>
<main class="canvas">
  <svg class="business-card" viewBox="0 0 259 143" preserveAspectRatio="none" xmlns="http://www.w3.org/2000/svg" aria-label="Corvella business card, front">
    <defs>
      <linearGradient id="base-fill" x1="0" y1="0" x2="1" y2="0">
        <stop offset="0" stop-color="#eef0f5"/>
        <stop offset="0.14" stop-color="#8aa3c0"/>
        <stop offset="0.32" stop-color="var(--card-slate)"/>
        <stop offset="0.75" stop-color="#3c6189"/>
        <stop offset="1" stop-color="#4d6282"/>
      </linearGradient>
      <linearGradient id="navy-fill" x1="0" y1="0" x2="1" y2="0">
        <stop offset="0" stop-color="#f1f1f6"/>
        <stop offset="0.3" stop-color="#4d5180"/>
        <stop offset="0.6" stop-color="var(--card-navy)"/>
        <stop offset="1" stop-color="#20244a"/>
      </linearGradient>
      <linearGradient id="silver-fill" x1="0" y1="0" x2="1" y2="0">
        <stop offset="0" stop-color="#f2f2f2"/>
        <stop offset="0.45" stop-color="#a8a8a8"/>
        <stop offset="1" stop-color="#0e0e0e"/>
      </linearGradient>
      <linearGradient id="taupe-fill" x1="0" y1="0" x2="1" y2="0">
        <stop offset="0" stop-color="#7d6656"/>
        <stop offset="0.6" stop-color="var(--card-taupe)"/>
        <stop offset="1" stop-color="#d9cbbd"/>
      </linearGradient>
      <linearGradient id="edge-fill" x1="0" y1="0" x2="1" y2="0">
        <stop offset="0" stop-color="#d8d8d8"/>
        <stop offset="0.5" stop-color="#6a6a6a"/>
        <stop offset="1" stop-color="#050505"/>
      </linearGradient>
    </defs>

    <rect class="card-base" x="0" y="0" width="259" height="143" fill="url(#base-fill)"/>
    <path class="corner-silver" d="M212,0 L259,0 L259,52 C244,40 224,22 212,0 Z" fill="url(#silver-fill)"/>
    <path class="corner-edge" d="M244,0 L259,0 L259,143 L248,143 C252,100 252,40 244,0 Z" fill="url(#edge-fill)" opacity="0.85"/>
    <path class="navy-swoosh" d="M0,112 C60,104 150,122 210,98 C236,87 250,70 259,52 L259,143 L0,143 Z" fill="url(#navy-fill)"/>
    <path class="taupe-swoosh" d="M150,140 C200,134 240,104 259,44 L259,143 L150,143 Z" fill="url(#taupe-fill)"/>
    <path class="base-shade" d="M182,143 C222,136 248,118 259,96 L259,143 Z" fill="url(#edge-fill)"/>

    <text class="brand-name" x="15" y="53" font-size="18">Corvella</text>
    <text class="person-name" x="208" y="52" font-size="27" text-anchor="end">NEL</text>
    <text class="credentials" x="208" y="66" font-size="7.8" text-anchor="end">BA (Psych)</text>
    <text class="credentials" x="208" y="77" font-size="7.8" text-anchor="end">BSc (Hons) Psychology</text>
    <text class="contact" x="208" y="92" font-size="7.8" text-anchor="end">Mobile: 0412 903 618</text>
    <text class="tagline" x="18" y="124" font-size="10.6">specialising in psychotherapy</text>
  </svg>
</main>
</body>
</html>
```